Marlow Estate Fixers (Handyman / Home Improvement Company)

Looking for a double sided professional looking business card with Logo attached to be highlighted on one side and throwing in an image of a handyman as an option would be nice to see as well. We are a company focused on providing quality Handyman and Home improvement services in a timely manner that is done right the first time with integrity

Industry/Entity Type

Handyman / Home Improvement

Contact Information for Business Card

(LOGO, Name, Mobile and office phone numbers, email) on front side of card, (the words "The SOLUTION to all of your Handyman and Home Improvement needs" followed by "Family Owned and Operated" at the very bottom) on the back.

Colors
EB3D1F
EC4F4E
F09395
F8D3D4
FCEDEE

Requirements
Must have
• Red, Gray, Black Color scheme
Should not have
• No Yellow or Blue colors

```html
<!DOCTYPE html>
<html lang="en">
<head>
<meta charset="utf-8">
<title>Marlow Estate Fixers – Business Card</title>
<link rel="stylesheet" href="https://fonts.googleapis.com/css2?family=Montserrat:wght@400;600;700;800&family=Oswald:wght@700&display=swap">
<style>
  :root {
    --brand-red: #e92b2f;
    --deep-red: #c4242a;
    --ink: #1d1d1f;
    --charcoal: #3b3b3e;
    --paper: #ffffff;
    --backdrop: #1e1e1f;
  }
  * { margin: 0; padding: 0; box-sizing: border-box; }
  html, body { width: 1200px; height: 1059px; overflow: hidden; }
  body {
    background: var(--backdrop);
    font-family: "Montserrat", Arial, sans-serif;
    position: relative;
  }
  .card { position: absolute; overflow: hidden; border-radius: 24px; }

  /* Front */
  .card-front {
    left: 251px; top: 96px; width: 700px; height: 400px;
    background: var(--paper);
  }
  .front-brand {
    position: absolute; left: 407px; top: 28px; width: 263px; height: 180px;
    display: flex; align-items: center; justify-content: center; gap: 12px;
  }
  .front-brand .brand-mark {
    width: 22px; height: 22px; background: var(--brand-red); flex: none;
  }
  .front-brand .brand-name {
    font-weight: 800; font-size: 30px; line-height: 1.1;
    color: var(--brand-red); text-transform: uppercase;
  }
  .holder-name {
    position: absolute; left: 35px; top: 241px;
    font-size: 28px; font-weight: 700; color: var(--brand-red);
  }
  .holder-role {
    position: absolute; left: 35px; top: 283px;
    font-size: 18px; font-weight: 400; color: var(--ink);
  }
  .front-rule {
    position: absolute; left: 35px; top: 321px; width: 636px; height: 2px;
    background: var(--charcoal);
  }
  .contact-row {
    position: absolute; left: 38px; top: 337px; right: 32px;
    display: flex; align-items: center; justify-content: space-between;
    font-size: 17.5px; color: var(--ink);
  }
  .contact-item { display: flex; align-items: center; gap: 10px; white-space: nowrap; }
  .contact-item svg { fill: var(--brand-red); flex: none; }
  .front-band {
    position: absolute; left: 0; bottom: 0; width: 100%; height: 12px;
  }

  /* Back */
  .card-back {
    left: 251px; top: 529px; width: 735px; height: 419px;
    background: var(--brand-red);
  }
  .back-tagline {
    position: absolute; left: 0; top: 24px; width: 100%;
    font-family: "Oswald", Impact, sans-serif; font-weight: 700;
    font-size: 37px; line-height: 45px; color: var(--paper);
    text-align: center; letter-spacing: -0.3px; white-space: nowrap;
  }
  .handyman-figure {
    position: absolute; left: 144px; top: 117px; width: 116px; height: 286px;
    border-radius: 6px;
    background: linear-gradient(180deg, var(--deep-red) 0%, #a81e24 100%);
  }
  .back-brand {
    position: absolute; left: 375px; top: 144px; width: 285px; height: 196px;
    display: flex; align-items: center; justify-content: center; gap: 12px;
  }
  .back-brand .brand-mark {
    width: 24px; height: 24px; background: var(--paper); flex: none;
  }
  .back-brand .brand-name {
    font-weight: 800; font-size: 34px; line-height: 1.1;
    color: var(--paper); text-transform: uppercase;
  }
  .back-footnote {
    position: absolute; left: 331px; top: 368px; width: 372px;
    font-size: 23px; font-weight: 700; color: var(--paper);
    text-align: center; white-space: nowrap;
  }
</style>
</head>
<body>

<section class="card card-front">
  <div class="front-brand">
    <span class="brand-mark"></span>
    <span class="brand-name">Marlow<br>Estate<br>Fixers</span>
  </div>

  <h1 class="holder-name">Daniel Reyes</h1>
  <p class="holder-role">Owner</p>
  <div class="front-rule"></div>

  <div class="contact-row">
    <span class="contact-item">
      <svg width="12" height="20" viewBox="0 0 12 20"><path d="M2 0h8a2 2 0 0 1 2 2v16a2 2 0 0 1-2 2H2a2 2 0 0 1-2-2V2a2 2 0 0 1 2-2zm0 2.5v13h8v-13zM6 16.3a1 1 0 1 0 0 2 1 1 0 0 0 0-2z"/></svg>
      044-987 654 321
    </span>
    <span class="contact-item">
      <svg width="19" height="16" viewBox="0 0 19 16"><path d="M1 5c0-3 4-4 8.5-4S18 2 18 5v1.5h-4V4.8c-1.5-.5-7.5-.5-9 0v1.7H1zM5 7h9l3 8H2z"/><rect x="7" y="9" width="5" height="4" fill="#fff"/></svg>
      044-987 654 321
    </span>
    <span class="contact-item">
      <svg width="18" height="13" viewBox="0 0 18 13"><path d="M0 0h18v1.5L9 7.5 0 1.5zM0 3.5l9 6 9-6V13H0z"/></svg>
      info@marlowfixers.com
    </span>
  </div>

  <svg class="front-band" viewBox="0 0 700 12" preserveAspectRatio="none">
    <polygon points="0,0 348,0 352,12 0,12" fill="var(--brand-red)"/>
    <polygon points="353,0 700,0 700,12 360,12" fill="var(--charcoal)"/>
  </svg>
</section>

<section class="card card-back">
  <h2 class="back-tagline">Your SOLUTION to all of<br>your Handyman and Home Improvement Needs</h2>

  <div class="handyman-figure" role="img" aria-label="Illustration of a handyman in work clothes holding a wrench"></div>

  <div class="back-brand">
    <span class="brand-mark"></span>
    <span class="brand-name">Marlow<br>Estate<br>Fixers</span>
  </div>

  <p class="back-footnote">Family Owned and Operated</p>
</section>

</body>
</html>
```